Elegant Business Card with Logo and Picture

Please create a business card that has the Logo colors add Gold and turquoise / use the attached logo - I would like a beautiful Business Card - Please make sure it's printed on both sides / Picture can go on one side Logo other
www.velmoragrove.com
614-372-0583
Lina Suzette Brolin
linasb@quorvamail.com
Life Coach
Thessing Certified Teacher / Life Coach / Interior Designer
Transformational Retreats

Target Market(s)

Women Men General

Industry/Entity Type

Life Coaching

Contact Information for Business Card

www.velmoragrove.com
614-372-0583
Lina Suzette Brolin
Life Coach
Thessing Certified Teacher / Yoga Teacher / Interior Designer

Font styles to use
Serif
Decorative

Colors
33a6d6
e34197
ffc214

Requirements
Must have
• Quality Paper and touch /
Nice to have
• Beautiful Touch and feel
Should not have
• needs to be elegant

```html
<!DOCTYPE html>
<html lang="en">
<head>
<meta charset="utf-8">
<title>Velmora Grove Coaching – Business Card</title>
<link rel="stylesheet" href="https://fonts.googleapis.com/css2?family=Roboto:wght@400;700&family=Roboto+Condensed:wght@500&family=Libre+Baskerville:wght@400&display=swap">
<style>
  :root {
    --backdrop: #1b1b1b;
    --pink-start: #ff0040;
    --pink-end: #f2077f;
    --pink: #e8176f;
    --gold: #ffc214;
    --turquoise: #33a6d6;
    --ink: #141414;
    --muted: #333333;
    --paper: #ffffff;
    --photo-light: #d9b48f;
    --photo-dark: #8a5a44;
  }
  * { box-sizing: border-box; margin: 0; padding: 0; }
  html, body { width: 1200px; height: 800px; overflow: hidden; }
  body { background: var(--backdrop); position: relative; font-family: "Roboto", sans-serif; }

  .card {
    position: absolute;
    width: 560px;
    height: 320px;
    border-radius: 24px;
    overflow: hidden;
    box-shadow: 0 14px 30px rgba(0,0,0,.45);
  }

  /* Front side */
  .card--front {
    left: 170px; top: 60px;
    background: linear-gradient(100deg, var(--pink-start) 0%, var(--pink-end) 100%);
    color: var(--paper);
  }
  .front-name {
    position: absolute; left: 48px; top: 112px;
    display: flex; align-items: center; gap: 14px;
  }
  .front-name__dot {
    width: 22px; height: 22px; border-radius: 50%;
    background: var(--gold); flex: none;
  }
  .front-name__text {
    font-family: "Roboto", sans-serif; font-weight: 700;
    font-size: 62px; line-height: 1; color: var(--paper);
  }
  .front-rule {
    position: absolute; left: 48px; top: 196px;
    width: 120px; height: 3px; background: var(--turquoise);
  }
  .front-brand {
    position: absolute; right: 30px; bottom: 28px; text-align: right;
  }
  .brand-name {
    font-family: "Libre Baskerville", serif; font-size: 15px;
    letter-spacing: 2.5px; text-transform: uppercase; white-space: nowrap;
  }
  .brand-sub {
    font-family: "Roboto", sans-serif; font-size: 7px;
    letter-spacing: 7px; text-transform: uppercase; margin-top: 3px;
  }
  .front-brand .brand-sub { color: var(--gold); }
  .front-brand .brand-url {
    font-family: "Roboto", sans-serif; font-size: 13px; letter-spacing: 1px; margin-top: 5px;
  }

  /* Back side */
  .card--back {
    left: 470px; top: 420px;
    background: var(--paper);
    color: var(--ink);
  }
  .portrait {
    position: absolute; left: 40px; top: 28px;
    width: 108px; height: 118px;
    border-radius: 14px;
    border: 2px solid #cfcfcf;
    background: linear-gradient(160deg, var(--photo-light), var(--photo-dark));
  }
  .profile { position: absolute; left: 40px; top: 158px; }
  .profile__name {
    font-family: "Roboto", sans-serif; font-weight: 700;
    font-size: 20px; color: var(--pink); margin-bottom: 4px;
  }
  .profile__roles {
    font-family: "Roboto Condensed", sans-serif; font-weight: 500;
    font-size: 13px; line-height: 1.25; color: var(--ink);
  }
  .contacts { list-style: none; margin-top: 8px; }
  .contacts li {
    display: flex; align-items: center; gap: 8px;
    font-size: 12.5px; line-height: 1.45; color: var(--muted);
  }
  .contacts svg { width: 12px; height: 12px; flex: none; }
  .icon-fill { fill: var(--pink); }
  .icon-line { fill: none; stroke: var(--pink); stroke-width: 2.4; stroke-linejoin: round; stroke-linecap: round; }

  .back-brand {
    position: absolute; right: 36px; top: 128px;
    display: flex; flex-direction: column; align-items: center;
  }
  .back-name {
    display: flex; align-items: center; gap: 8px; margin-bottom: 12px;
  }
  .back-name__dot {
    width: 12px; height: 12px; border-radius: 50%; background: var(--turquoise); flex: none;
  }
  .back-name__text {
    font-family: "Roboto", sans-serif; font-weight: 700; font-size: 28px; line-height: 1; color: var(--ink);
  }
  .back-brand .brand-name { color: var(--ink); font-size: 14px; }
  .back-brand .brand-sub { color: var(--pink); }
  .back-rule { width: 60px; height: 2px; background: var(--gold); margin-top: 8px; }
</style>
</head>
<body>

<section class="card card--front" aria-label="Business card front">
  <div class="front-name">
    <span class="front-name__dot"></span>
    <span class="front-name__text">Velmora</span>
  </div>
  <div class="front-rule"></div>
  <div class="front-brand">
    <p class="brand-name">Velmora Grove</p>
    <p class="brand-sub">Coaching</p>
    <p class="brand-url">www.velmoragrove.com</p>
  </div>
</section>

<section class="card card--back" aria-label="Business card back">
  <div class="portrait" role="img" aria-label="Portrait photograph of Lina Suzette Brolin"></div>

  <div class="profile">
    <h1 class="profile__name">Lina Suzette Brolin</h1>
    <p class="profile__roles">Life Coach<br>Thessing Certified Teacher /<br>Yoga Teacher / Interior Designer</p>
    <ul class="contacts">
      <li>
        <svg viewBox="0 0 24 24" aria-hidden="true"><path class="icon-fill" d="M6.6 10.8a15.1 15.1 0 0 0 6.6 6.6l2.2-2.2a1 1 0 0 1 1-.25 11.4 11.4 0 0 0 3.6.57 1 1 0 0 1 1 1V20a1 1 0 0 1-1 1A17 17 0 0 1 3 4a1 1 0 0 1 1-1h3.5a1 1 0 0 1 1 1c0 1.25.2 2.45.57 3.57a1 1 0 0 1-.25 1z"/></svg>
        614-372-0583
      </li>
      <li>
        <svg viewBox="0 0 24 24" aria-hidden="true"><rect class="icon-line" x="3" y="5" width="18" height="14" rx="1"/><path class="icon-line" d="M3 6l9 7 9-7"/></svg>
        linasb@quorvamail.com
      </li>
      <li>
        <svg viewBox="0 0 24 24" aria-hidden="true"><circle class="icon-line" cx="12" cy="12" r="9"/><path class="icon-line" d="M3 12h18M12 3c3 3 3 15 0 18M12 3c-3 3-3 15 0 18"/></svg>
        www.velmoragrove.com
      </li>
    </ul>
  </div>

  <div class="back-brand">
    <div class="back-name">
      <span class="back-name__dot"></span>
      <span class="back-name__text">Velmora</span>
    </div>
    <p class="brand-name">Velmora Grove</p>
    <p class="brand-sub">Coaching</p>
    <div class="back-rule"></div>
  </div>
</section>

</body>
</html>
```